Automotive component supplier needs a business card design

We need a business card design for our company called Velran Global Components Ltd based in the UK. We are a supplier of interior and exterior components to premium car manufacturers such as Corvel Ashby, Hadley Fenn, Marquist and Tavarelli. We would like to see a modern business card design that uses the colour blue.

Target Market(s)

Premium automotive car manufacturers.

Industry/Entity Type

Automotive

Contact Information for Business Card

Company Name : Velran Global Components Limited
Address: 17 Marlow Yard, Upper Heath, Warwick, CV31 8QL, United Kingdom
Web Address : www.velrancomponents-example.co.uk

Font styles to use
Other font styles liked:
• Helvetica

Colors
3176b5
0255a3
85acd3
cfdeed
cee9f5
85cae6
34a6d7
0692cd
9bcb3c

Requirements
Must have
• Clear company logo and a mixture of blue colours.
Nice to have
• A high quality modern image.
Should not have
• Multiple colours.

```html
<!DOCTYPE html>
<html lang="en">
<head>
<meta charset="utf-8">
<title>Velran Global Components – Business Card</title>
<link rel="stylesheet" href="https://fonts.googleapis.com/css2?family=Exo+2:wght@400;500;700;800&display=swap">
<style>
  :root {
    --blue-deep: #0255a3;
    --blue-mid: #3176b5;
    --blue-soft: #85acd3;
    --blue-pale: #cfdeed;
    --green: #9bcb3c;
    --card: #eef2f5;
    --ink: #4a4f55;
    --backdrop: #d8d5cf;
  }
  html, body {
    margin: 0;
    padding: 0;
    width: 1200px;
    height: 969px;
    overflow: hidden;
    background: var(--backdrop);
    font-family: "Exo 2", "Helvetica Neue", Arial, sans-serif;
  }
  .card {
    position: absolute;
    left: 120px;
    top: 212px;
    width: 960px;
    height: 546px;
    background: var(--card);
    border-radius: 4px;
    box-shadow: 0 6px 24px rgba(0,0,0,0.18);
    overflow: hidden;
  }
  .brand {
    position: absolute;
    left: 53px;
    top: 62px;
    color: var(--blue-deep);
    font-weight: 700;
    line-height: 1;
  }
  .brand-name {
    display: block;
    font-size: 82px;
    letter-spacing: 2px;
  }
  .brand-tagline {
    display: block;
    font-size: 23px;
    letter-spacing: 1.5px;
    margin-top: 6px;
  }
  .name-band {
    position: absolute;
    left: 0;
    top: 243px;
    width: 855px;
    height: 93px;
    background: linear-gradient(90deg, var(--blue-mid) 0%, var(--blue-deep) 100%);
  }
  .person-name {
    position: absolute;
    left: 53px;
    top: 12px;
    margin: 0;
    color: #fff;
    font-size: 33px;
    font-weight: 700;
    letter-spacing: 1px;
  }
  .person-role {
    position: absolute;
    left: 55px;
    top: 55px;
    margin: 0;
    color: var(--blue-pale);
    font-size: 23px;
    font-weight: 400;
    letter-spacing: 0.5px;
  }
  .accent-tile {
    position: absolute;
    left: 860px;
    top: 243px;
    width: 93px;
    height: 93px;
    border-radius: 12px;
    background: var(--green);
  }
  .contact-list {
    position: absolute;
    left: 53px;
    top: 368px;
    margin: 0;
    padding: 0;
    list-style: none;
    color: var(--ink);
    font-size: 24px;
  }
  .contact-list li {
    display: flex;
    align-items: center;
    height: 37px;
  }
  .contact-list svg {
    width: 22px;
    height: 22px;
    margin-right: 14px;
    fill: var(--blue-deep);
    flex: none;
  }
  .address {
    position: absolute;
    right: 50px;
    top: 408px;
    margin: 0;
    text-align: right;
    font-style: normal;
    color: var(--ink);
    font-size: 24px;
    line-height: 34px;
  }
</style>
</head>
<body>
  <main class="card">
    <div class="brand">
      <span class="brand-name">VELRAN</span>
      <span class="brand-tagline">GLOBAL COMPONENTS</span>
    </div>

    <div class="name-band">
      <h1 class="person-name">DANIEL HARLOW</h1>
      <p class="person-role">CEO/Founder</p>
    </div>
    <div class="accent-tile"></div>

    <ul class="contact-list">
      <li>
        <svg viewBox="0 0 24 24" aria-hidden="true"><path d="M6.6 10.8a15.2 15.2 0 0 0 6.6 6.6l2.2-2.2c.3-.3.7-.4 1-.2 1.1.4 2.3.6 3.6.6.6 0 1 .4 1 1V20c0 .6-.4 1-1 1A17 17 0 0 1 3 4c0-.6.4-1 1-1h3.5c.6 0 1 .4 1 1 0 1.3.2 2.5.6 3.6.1.3 0 .7-.2 1z"/></svg>
        604 218 7351
      </li>
      <li>
        <svg viewBox="0 0 24 24" aria-hidden="true"><path d="M7 1h10a2 2 0 0 1 2 2v18a2 2 0 0 1-2 2H7a2 2 0 0 1-2-2V3a2 2 0 0 1 2-2zm0 3v14h10V4zm5 15.2a1.2 1.2 0 1 0 0 2.4 1.2 1.2 0 0 0 0-2.4z"/></svg>
        812 593 4076
      </li>
      <li>
        <svg viewBox="0 0 24 24" aria-hidden="true"><path d="M2 5h20v14H2zm2 2v.4l8 5.2 8-5.2V7zm0 2.8V17h16V9.8l-8 5.2z"/></svg>
        daniel@velrancomponents-example.co.uk
      </li>
      <li>
        <svg viewBox="0 0 24 24" aria-hidden="true"><path d="M12 2a10 10 0 1 0 0 20 10 10 0 0 0 0-20zm-1 17.9A8 8 0 0 1 4.2 10.8L9 15.6v1a2 2 0 0 0 2 2zm6.9-2.5A2 2 0 0 0 16 16h-1v-3a1 1 0 0 0-1-1H8v-2h2a1 1 0 0 0 1-1V7h2a2 2 0 0 0 2-2v-.4a8 8 0 0 1 2.9 12.8z"/></svg>
        www.velrancomponents-example.co.uk
      </li>
    </ul>

    <address class="address">
      17 Marlow Yard, Upper Heath<br>
      Warwick, CV31 8QL<br>
      United Kingdom
    </address>
  </main>
</body>
</html>
```